Form With Marla - Health and Wellness Business Card and Logo

I need a business card design with a logo for my business you can check out at www.formwithmarla.net. I want something more original, simplistic, and memorable than the basic logo I have on my site currently. I am a health and wellness coach and I offer mindset coaching and nutrition plans. I like the colour teal and dark grey/black for my theme colours. I emphasize growth, longterm change, and the whole package of "healthy mind, healthy body, healthy life". I had played around the idea of intertwining 3 M's or incorporating growth (leaves etc.) into my design. I want my expertise and experience to show through. In one glance I want people to understand with confidence I can help them accomplish anything they set their minds to. I look forward to seeing what everyone comes up with!

Industry/Entity Type

Health And Wellness

Contact Information for Business Card

Form With Marla
Marla Prentiss
BSc, Health & Wellness Coach
"Manifest your best"
www.formwithmarla.net
formwithmarla@quillpost.net
472-618-9043

Colors
33b8a4
ffffff
333333
000000

Requirements
Must have
• A memorable and unique logo for my business!
Nice to have
• Could have the phrase "Are you unhappy with your body and state of health?" or "It takes the right skills to develop habits in order to create long term change. I can help you get there."

```html
<!DOCTYPE html>
<html lang="en">
<head>
<meta charset="utf-8">
<title>Form With Marla – Business Card</title>
<link href="https://fonts.googleapis.com/css2?family=Exo+2:ital,wght@0,400;0,600;0,700;0,800;1,800&display=swap" rel="stylesheet">
<style>
  :root {
    --teal: #1f8d80;
    --teal-deep: #0f5f58;
    --teal-light: #2a9b8f;
    --ink: #3a3a3a;
    --muted: #5a5a5a;
    --paper: #ffffff;
    --mark-grey: #d8dcdb;
    --backdrop: #e6e8e8;
  }
  * { margin: 0; padding: 0; box-sizing: border-box; }
  html, body {
    width: 1200px; height: 1000px; overflow: hidden;
    background: var(--backdrop);
    font-family: "Exo 2", sans-serif;
  }
  .canvas {
    width: 1200px; height: 1000px;
    display: flex; flex-direction: column; align-items: center; justify-content: center;
    gap: 60px;
  }
  .card {
    position: relative;
    width: 700px; height: 400px;
    border-radius: 22px;
    overflow: hidden;
    box-shadow: 0 14px 34px rgba(0,0,0,0.18);
  }

  /* Front */
  .card-front { background: linear-gradient(160deg, #f1f1f1 0%, var(--paper) 45%); }
  .holder {
    position: absolute; left: 48px; top: 92px;
  }
  .holder-name {
    color: var(--teal);
    font-weight: 800; font-style: italic;
    font-size: 31px; letter-spacing: 0.5px;
    text-transform: uppercase; line-height: 1;
  }
  .holder-role {
    display: flex; align-items: flex-end; gap: 6px;
    margin-top: 4px;
    color: var(--muted); font-size: 19px; line-height: 1;
  }
  .rule {
    position: absolute; left: 140px; top: 124px;
    width: 400px; height: 2px; background: var(--teal);
  }
  .contacts {
    position: absolute; left: 48px; top: 150px;
    list-style: none;
    color: var(--ink); font-size: 16px; line-height: 26px;
  }
  .contacts li { display: flex; align-items: center; gap: 12px; }
  .contacts svg { width: 12px; height: 12px; fill: var(--teal-deep); flex: none; }
  .contacts .accent { color: var(--teal); }
  .address {
    position: absolute; right: 60px; bottom: 44px;
    text-align: right; color: var(--ink); font-size: 17px; line-height: 24px;
  }
  .front-mark {
    position: absolute; right: 60px; top: 150px;
    display: flex; flex-direction: column; align-items: center; gap: 8px;
  }
  .mark-circle {
    width: 86px; height: 86px; border-radius: 50%;
    border: 3px solid var(--teal);
  }
  .front-mark .brand-name {
    color: var(--teal); font-weight: 700; font-size: 15px; letter-spacing: 1px;
  }

  /* Back */
  .card-back {
    background: radial-gradient(ellipse at 35% 30%, var(--teal-light) 0%, var(--teal) 45%, var(--teal-deep) 100%);
    display: flex; flex-direction: column; align-items: center; justify-content: center;
    gap: 26px;
  }
  .card-back .mark-circle {
    width: 150px; height: 150px; border: 4px solid var(--mark-grey);
  }
  .card-back .brand-name {
    color: var(--mark-grey); font-weight: 700; font-size: 30px; letter-spacing: 3px;
  }
</style>
</head>
<body>
<main class="canvas">
  <section class="card card-front" aria-label="Business card front">
    <div class="holder">
      <h1 class="holder-name">Marla Prentiss</h1>
      <p class="holder-role">Director</p>
    </div>
    <div class="rule"></div>
    <ul class="contacts">
      <li>
        <svg viewBox="0 0 12 12" aria-hidden="true"><path d="M2.5 0.5 L4.5 3 L3.4 4.3 C4 5.8 6.2 8 7.7 8.6 L9 7.5 L11.5 9.5 L10.3 11.3 C5.5 11 1 6.5 0.7 1.7 Z"/></svg>
        +000 123 456 789
      </li>
      <li>
        <svg viewBox="0 0 12 12" aria-hidden="true"><path d="M0.5 2 H11.5 V10 H0.5 Z M1.3 2.6 L6 6.6 L10.7 2.6 Z" fill-rule="evenodd"/></svg>
        yourname@email.com
      </li>
      <li>
        <svg viewBox="0 0 12 12" aria-hidden="true"><circle cx="6" cy="6" r="5.5"/><path d="M0.8 6 H11.2 M6 0.6 C3.6 3 3.6 9 6 11.4 M6 0.6 C8.4 3 8.4 9 6 11.4" stroke="#fff" stroke-width="0.9" fill="none"/></svg>
        <span>www.<span class="accent">websitename</span>.com</span>
      </li>
    </ul>
    <div class="front-mark">
      <div class="mark-circle"></div>
      <span class="brand-name">formwithmarla</span>
    </div>
    <p class="address">Your Street Address,<br>Singapore, 1234</p>
  </section>

  <section class="card card-back" aria-label="Business card back">
    <div class="mark-circle"></div>
    <span class="brand-name">formwithmarla</span>
  </section>
</main>
</body>
</html>
```